Automotive Repair Christmas Incentive Offer

We are an automotive repair shop that specializes in import auto repair. We need a postcard mailer that will target pre-existing customers for the Holiday season. On the front, we would like an image of a happy, female customer that is pointing to a message of holiday wishes with our company. The colors should be a traditional holiday theme with the predominant color being red. We would like the visual trail to start at the female's face and then travel to her finger pointing to the Happy Holidays message. On the reverse side, we would like to have the text read like the attached PDF file.

Target Market(s)

Females, 25-45, average household income $100000.00/year, college educated, kids in famile

Industry/Entity Type

Automotive

Font styles to use
Serif

Colors
ec1f27
9bcb3c
000000

Requirements
Must have
• Simple lines, clear and attractive font, be NPDC approved format for mailing, attractive images that are polished looking and high-quality, holiday colors
Should not have
• Cluttered images, hard to read font, complicated color schemes

```html
<!DOCTYPE html>
<html lang="en">
<head>
<meta charset="utf-8">
<title>Happy Holidays – Halden's Auto</title>
<link rel="stylesheet" href="https://fonts.googleapis.com/css2?family=Crimson+Text:ital,wght@1,400&family=EB+Garamond:wght@600&display=swap">
<style>
  :root {
    --holiday-green: #5cf500;
    --tag-green: #4fd61a;
    --gift-red: #ee1c1c;
    --gift-red-light: #f5372f;
    --gift-red-dark: #c80f0f;
    --gift-red-deep: #a80a0a;
    --brand-red: #c21a1f;
    --backdrop-light: #f3f3f4;
    --backdrop-grey: #e3e4e6;
    --ink: #000000;
    --paper: #ffffff;
    --bow-gold-light: #e6d3a4;
    --bow-gold: #b8a074;
    --bow-gold-dark: #7d6a45;
  }
  * { margin: 0; padding: 0; box-sizing: border-box; }
  html, body { width: 1200px; height: 773px; overflow: hidden; }
  .postcard {
    position: relative;
    width: 1200px;
    height: 773px;
    overflow: hidden;
    background: radial-gradient(ellipse at 60% 40%, var(--backdrop-light), var(--backdrop-grey));
  }
  .green-band {
    position: absolute;
    left: 0; top: 0;
    width: 266px; height: 773px;
    background: var(--holiday-green);
  }
  .gift-art {
    position: absolute;
    left: 0; top: 0;
    width: 1200px; height: 773px;
  }
  .gift-tag-text {
    position: absolute;
    left: 250px; top: 108px;
    width: 250px;
    text-align: center;
    font-family: "Crimson Text", serif;
    font-style: italic;
    font-weight: 400;
    line-height: 42px;
  }
  .gift-tag-text span { display: block; }
  .tag-accent { color: var(--tag-green); font-size: 44px; }
  .tag-main { color: var(--ink); font-size: 46px; }
  .holiday-greeting {
    position: absolute;
    left: 40px; top: 306px;
    width: 500px;
    text-align: center;
    color: var(--paper);
    font-family: "Crimson Text", serif;
    font-style: italic;
    font-weight: 400;
    font-size: 66px;
    line-height: 1;
    white-space: nowrap;
  }
  .company-name {
    position: absolute;
    left: 46px; top: 530px;
    font-family: "EB Garamond", serif;
    font-weight: 600;
    font-size: 86px;
    line-height: 1;
    color: var(--brand-red);
    white-space: nowrap;
  }
  .customer-photo {
    position: absolute;
    left: 580px; top: 100px;
    width: 548px; height: 673px;
    background: linear-gradient(180deg, rgba(230,40,40,0.16) 0%, rgba(245,240,236,0.55) 45%, rgba(220,30,30,0.32) 100%);
  }
</style>
</head>
<body>
<main class="postcard">
  <div class="green-band"></div>

  <div class="customer-photo" role="img" aria-label="Photo of a smiling woman in a Santa hat, red scarf and red skirt pointing toward the holiday greeting"></div>

  <svg class="gift-art" viewBox="0 0 1200 773" aria-hidden="true">
    <defs>
      <linearGradient id="lid-shade" x1="0" y1="0" x2="0" y2="1">
        <stop offset="0" stop-color="var(--gift-red-light)"/>
        <stop offset="1" stop-color="var(--gift-red)"/>
      </linearGradient>
      <linearGradient id="front-shade" x1="0" y1="0" x2="0" y2="1">
        <stop offset="0" stop-color="var(--gift-red-dark)"/>
        <stop offset="1" stop-color="var(--gift-red-deep)"/>
      </linearGradient>
    </defs>
    <polygon class="gift-top" points="77,132 540,132 546,412 26,412" fill="url(#lid-shade)"/>
    <polygon class="gift-front" points="26,412 546,412 546,472 48,472" fill="url(#front-shade)"/>
    <polygon class="gift-right-edge" points="540,132 548,140 552,472 546,472 546,412" fill="var(--gift-red-deep)"/>
    <line class="gift-edge-highlight" x1="26" y1="412" x2="546" y2="412" stroke="var(--gift-red-light)" stroke-width="2"/>
    <rect class="gift-tag" x="244" y="94" width="274" height="206" rx="16" fill="var(--paper)" stroke="var(--tag-green)" stroke-width="7"/>
  </svg>

  <svg class="gift-art" viewBox="0 0 1200 773" role="img" aria-label="Gold ribbon bow on the gift box">
    <defs>
      <radialGradient id="bow-gold" cx="0.45" cy="0.4" r="0.7">
        <stop offset="0" stop-color="var(--bow-gold-light)"/>
        <stop offset="0.6" stop-color="var(--bow-gold)"/>
        <stop offset="1" stop-color="var(--bow-gold-dark)"/>
      </radialGradient>
    </defs>
    <rect x="38" y="92" width="218" height="208" rx="34" fill="url(#bow-gold)"/>
  </svg>

  <div class="gift-tag-text">
    <span class="tag-accent">From</span>
    <span class="tag-main">Our Family</span>
    <span class="tag-accent">To</span>
    <span class="tag-main">Yours</span>
  </div>

  <h1 class="holiday-greeting">Happy Holidays</h1>

  <p class="company-name">Halden’s Auto</p>
</main>
</body>
</html>
```